WP website design (Wellacombe)

We need a wordpress design for an established auction and real estate company based in Viginia- "The Bid That Counts!". The winning design will incorporate a professional color scheme with company logo in a clean layout. The design needs to consider that this will be developed on a responsive theme.
Industry/Entity Type
Real Estate
Requirements
Must have
- - - We will require winning designer to provide a layered PSD (Adobe photoshop) concept file, along with any non-standard font files used.
- Logo attached. Color scheme should compliment the logo colors; nothing flashy, rather more business oriented … subdued colors. Lighten up the burgundy color; not so dark on the background;
- Horizontal Navigation menu with these pages:
- Home - Upcoming Auctions - Appraisals - Past Auctions - Real Estate for Sale Sellers - Buyers - About Wellacombe - Contact Us
- A slideshow element on the home page use stock of real estate for the initial image.
- Sidebar widgets to be included are: Email sign-up form - Featured Auctions - Testimonial widget - 'Our Videos' widget; Social media icons somewhere in layout (facebook, twitter, RSS, and Youtube, linkedIn), News & Events widget, "Special announcements" blog.
- Homepage content is text:
- Wellacombe is "The bid that counts!"
- Wellacombe Auctioneers International is a premier, full service Auction Company specializing in the sale of commercial and residential real estate through the auction method. In the last 53 years, we have conducted thousands of auctions across the United States and several foreign countries.
- We bring our years of experience in auctioning homes, land, condominiums, industrial properties, retail buildings and development sites to help private individuals, corporations and financial institutions sell their property. In addition, we can assist you with liquidating estates, antiques, equipment and firearms collections.
- We have conducted thousands of auctions, assisting a wide range of companies both large and small achieve maximum value for their capital assets.
Nice to have
- Site will have drop down menus, please show what one will look like.
Should not have
- no gavels should be used in the design

```html
<!DOCTYPE html>
<html lang="en">
<head>
<meta charset="utf-8">
<title>Wellacombe Auctioneers International</title>
<link rel="stylesheet" href="https://fonts.googleapis.com/css2?family=Arimo:wght@400;700&family=Libre+Baskerville:ital@0;1&display=swap">
<style>
:root{
  --red:#c4242b;
  --navy:#2b3f86;
  --ink:#2b2b2b;
  --panel:#f1f1f1;
  --line:#d6d6d6;
  --footer:#1f1f1f;
  --footer-ink:#bdbdbd;
}
*{box-sizing:border-box;margin:0;padding:0}
html,body{width:1095px;height:1200px;overflow:hidden}
body{position:relative;font-family:"Arimo",Arial,sans-serif;color:var(--ink);
  background:linear-gradient(#e6eaf3 0,#f4f5f9 300px,#fafafa 600px)}
.abs{position:absolute}
.serif{font-family:"Libre Baskerville",Georgia,serif}

.brand{left:96px;top:22px;width:260px;height:84px}
.brand-mark{left:0;top:4px;width:38px;height:38px;border-radius:50%;background:var(--navy)}
.brand-name{left:48px;top:2px;font-weight:700;color:var(--red);font-size:18px;line-height:21px;letter-spacing:.3px}
.brand-tag{left:48px;top:48px;font-size:9px;color:#444}
.brand-partner{left:48px;top:62px;font-size:9px;color:#444}

.nav{left:93px;top:119px;width:909px;height:42px;background:var(--red);border-radius:5px 5px 0 0;display:flex}
.nav a{color:#fff;text-decoration:none;font-size:11.5px;font-weight:700;display:flex;align-items:center;justify-content:center;border-right:1px solid #e25359;height:100%}
.nav a:last-child{border-right:0}
.nav a.active{background:var(--navy)}
.dropdown{left:324px;top:161px;width:154px;background:var(--navy);border-radius:0 0 5px 5px;z-index:3;opacity:.96}
.dropdown a{display:block;color:#fff;text-decoration:none;font-size:11.5px;font-weight:700;padding:7px 17px;border-bottom:1px solid #44589a}
.dropdown a:last-child{border-bottom:0}

.hero{left:94px;top:162px;width:638px;height:279px;background:linear-gradient(100deg,#c9cfd2 0,#d8d3c4 30%,#b9a891 55%,#ece9e4 80%,#f7f7f7 100%)}
.featured{left:734px;top:162px;width:268px;height:279px;background:var(--navy);color:#fff;padding:0 18px}
.featured h2{font-family:"Libre Baskerville",serif;font-style:italic;font-weight:400;font-size:21px;padding:16px 0 8px;border-bottom:1px solid #7a89bb}
.featured .title{font-size:12.5px;margin-top:14px}
.featured .photo{margin-top:7px;width:231px;height:94px;border:2px solid #98a5cc;background:linear-gradient(180deg,#a7c6e6,#8aa46b 70%,#6d7f47)}
.featured p{font-size:11.5px;line-height:17px;margin-top:4px;max-width:215px}
.featured p:first-of-type{margin-top:26px}

.intro{left:94px;top:464px;width:620px;font-size:16.5px;line-height:25px;font-style:italic;color:#333;padding-bottom:12px;border-bottom:1px solid var(--line)}
.section-title{left:93px;top:530px;font-style:italic;font-weight:400;font-size:21px;color:var(--red)}

.card{left:93px;width:616px;height:245px;background:var(--panel);border:1px solid #dadada;border-radius:6px 6px 0 0}
.card-head{height:37px;background:var(--navy);border-radius:6px 6px 0 0;color:#fff;font-size:14px;letter-spacing:.5px;padding:11px 12px}
.thumb{left:9px;top:52px;width:117px;height:96px;background:#fff;border:1px solid var(--line);border-radius:5px;padding:8px 7px}
.thumb div{width:100%;height:100%;background:linear-gradient(180deg,#b9d3ec 0,#c8d8e6 35%,#7f9a5a 60%,#5f7d3b 100%)}
.desc{left:139px;top:52px;width:459px;height:96px;background:#fff;border:1px solid var(--line);border-radius:5px;padding:9px 7px;font-size:11.5px;line-height:16.5px;color:#222}
.desc .hl{color:#d8141c;font-weight:700}
.details{left:11px;top:164px;width:113px;height:33px;background:linear-gradient(#333,#000);border:2px solid #bbb;border-radius:6px;color:#fff;font-size:15px;display:flex;align-items:center;padding-left:10px;gap:8px}
.when{left:139px;top:158px;width:459px;height:75px;background:#fff;border:1px solid var(--line);border-radius:5px;padding:9px 7px;font-size:12.5px;line-height:17px;color:#222}
.when .gap{margin-top:5px}

.sidebar{left:733px;top:455px;width:269px;height:627px;background:var(--panel);border:1px solid #dadada}
.side-block{padding:0 7px 0 14px}
.side-h{font-family:"Libre Baskerville",serif;font-style:italic;font-weight:400;color:var(--red);font-size:21px}
.rule{height:1px;background:#ccc;margin:0 7px}
.signup p{font-size:12px;line-height:16.5px;color:#333;margin-top:8px;letter-spacing:.2px;max-width:225px}
.form{display:flex;margin-top:11px;width:239px;height:27px}
.form span{flex:1;background:#fff;border:1px solid #c7c7c7;font-size:11px;color:#555;padding:6px 7px}
.form b{width:47px;background:var(--navy);color:#fff;font-size:13px;display:flex;align-items:center;justify-content:center;border-radius:0 8px 8px 0}
.video{margin:14px 0 0 9px;width:248px;height:169px;position:relative;background:linear-gradient(180deg,#3f80c8 0,#7fb0dc 35%,#c8a88a 60%,#a0643c 85%,#6b4b35 100%)}
.video .bar{position:absolute;left:0;bottom:0;width:100%;height:17px;background:#111}
.news a{display:block;font-size:11.5px;line-height:15px;color:#333;text-decoration:none;margin-top:8px;max-width:240px}
.social{display:flex;gap:11px;margin:19px 0 0 20px}
.social span{width:37px;height:38px;border-radius:4px;background:var(--navy);color:#fff;font-size:8px;font-weight:700;display:flex;align-items:center;justify-content:center}

.footer{left:0;top:1110px;width:1095px;height:90px;background:var(--footer);color:#fff}
.footer nav{position:absolute;left:99px;top:24px;font-size:11.5px}
.footer nav a{color:#fff;text-decoration:none}
.footer nav i{font-style:normal;margin:0 6px}
.footer .copy{position:absolute;left:99px;top:49px;font-size:11.5px}
.footer .brand{left:820px;top:14px}
.footer .brand-mark{background:#4a4a4a}
.footer .brand-name,.footer .brand-tag,.footer .brand-partner{color:var(--footer-ink)}
</style>
</head>
<body>

<header class="brand abs">
  <div class="brand-mark abs"></div>
  <div class="brand-name abs">WELLACOMBE<br>AUCTIONEERS</div>
  <div class="brand-tag abs">"The Bid That Counts!"</div>
  <div class="brand-partner abs">an alliance partner of Meridian Global</div>
</header>

<nav class="nav abs">
  <a style="width:72px">HOME</a>
  <a style="width:159px">UPCOMING AUCTIONS</a>
  <a class="active" style="width:137px">ONLINE AUCTIONS</a>
  <a style="width:111px">REAL ESTATE</a>
  <a style="width:95px">SERVICES</a>
  <a style="width:91px">ABOUT US</a>
  <a style="width:147px">AUCTION GALLERY</a>
  <a style="flex:1">CONTACT</a>
</nav>
<div class="dropdown abs">
  <a>Wellacombe</a>
  <a>Auctioneers</a>
  <a>Auctioneers</a>
</div>

<div class="hero abs" role="img" aria-label="Stock photo of a hand holding a model house in front of a blurred residential building"></div>

<aside class="featured abs">
  <h2>Featured Auctions</h2>
  <div class="title">Multi Estate &amp; Consignment Auction</div>
  <div class="photo" role="img" aria-label="Photo of an agent standing in front of a suburban home"></div>
  <p><b>Start Date/ Time:</b> Saturday, April 13, 2013 At 10:00 Am</p>
  <p><b>Location:</b> 1180 Cedar Ridge, OK</p>
</aside>

<p class="intro abs serif">We have conducted thousands of auctions, assisting a wide range of companies both large and small achieve maximum value for their capital assets.</p>
<h2 class="section-title abs serif">Upcoming Auctions</h2>

<article class="card abs" style="top:573px">
  <div class="card-head serif">160± ACRES LAND NOBLE COUNTY, OK</div>
  <div class="thumb abs"><div role="img" aria-label="Photo of a farmhouse on open land"></div></div>
  <div class="desc abs">HARLOW AREA * CROP &amp; TIMBER<br><span class="hl">160± ACRES LAND NOBLE COUNTY</span><b>, OK ~ HARLOW AREA * CROP &amp;<br>TIMBER ~ EXCELLENT HUNTING</b><br>SELLER: THE PRAIRIE HERITAGE FOUNDATION</div>
  <div class="details abs"><svg width="18" height="18" viewBox="0 0 18 18"><circle cx="7.5" cy="7.5" r="5.5" fill="#cfe3f4" stroke="#fff" stroke-width="1.6"/><path d="M11.5 11.5l5 5" stroke="#fff" stroke-width="2.4" stroke-linecap="round"/></svg>Details</div>
  <div class="when abs">Begins:&nbsp; Tuesday, March 12, 2013 at 10:00 AM CDT<div class="gap"><b>Location:</b>&nbsp; See Directions</div>United States Harlow, OK 74611</div>
</article>

<article class="card abs" style="top:837px">
  <div class="card-head serif">160± ACRES LAND NOBLE COUNTY, OK</div>
  <div class="thumb abs"><div role="img" aria-label="Photo of a farmhouse on open land"></div></div>
  <div class="desc abs">HARLOW AREA * CROP &amp; TIMBER<br><span class="hl">160± ACRES LAND NOBLE COUNTY</span><b>, OK ~ HARLOW AREA * CROP &amp;<br>TIMBER ~ EXCELLENT HUNTING</b><br>SELLER: THE PRAIRIE HERITAGE FOUNDATION</div>
  <div class="details abs"><svg width="18" height="18" viewBox="0 0 18 18"><circle cx="7.5" cy="7.5" r="5.5" fill="#cfe3f4" stroke="#fff" stroke-width="1.6"/><path d="M11.5 11.5l5 5" stroke="#fff" stroke-width="2.4" stroke-linecap="round"/></svg>Details</div>
  <div class="when abs">Begins:&nbsp; Tuesday, March 12, 2013 at 10:00 AM CDT<div class="gap"><b>Location:</b>&nbsp; See Directions</div>United States Harlow, OK 74611</div>
</article>

<aside class="sidebar abs">
  <div class="side-block signup" style="padding-top:13px;padding-bottom:20px">
    <h3 class="side-h">Email Sign Up</h3>
    <p>Sign up to receive exclusive email updates for upcoming auctions</p>
    <div class="form"><span>Email Address</span><b>Join</b></div>
  </div>
  <div class="rule"></div>
  <div class="video" role="img" aria-label="Video still of a large Mediterranean-style home with palm trees">
    <svg class="abs" style="left:100px;top:54px" width="48" height="48" viewBox="0 0 48 48"><circle cx="24" cy="24" r="24" fill="rgba(0,0,0,.55)"/><path d="M19 14l16 10-16 10z" fill="#fff"/></svg>
    <div class="bar">
      <svg width="248" height="17" viewBox="0 0 248 17"><path d="M9 4l7 4.5-7 4.5z" fill="#fff"/><rect x="27" y="7" width="86" height="4" rx="2" fill="#666"/><rect x="27" y="5" width="5" height="8" rx="1" fill="#eee"/><text x="122" y="12" fill="#ccc" font-size="8" font-family="Arimo,sans-serif">00:00 / 04:36</text><path d="M178 6h3l3-3v11l-3-3h-3z" fill="#fff"/><rect x="187" y="5" width="2" height="7" fill="#fff"/><rect x="191" y="5" width="2" height="7" fill="#fff"/><rect x="195" y="5" width="2" height="7" fill="#fff"/><circle cx="214" cy="6" r="2" fill="#fff"/><circle cx="214" cy="12" r="2" fill="#fff"/><circle cx="208" cy="9" r="2" fill="#fff"/><path d="M208 9l6-3M208 9l6 3" stroke="#fff"/><path d="M226 4v4M226 4h4M238 4v4M238 4h-4M226 13v-4M226 13h4M238 13v-4M238 13h-4" stroke="#fff" stroke-width="1.5"/></svg>
    </div>
  </div>
  <div class="rule" style="margin-top:17px"></div>
  <div class="side-block news" style="padding-top:9px;padding-bottom:12px">
    <h3 class="side-h">News &amp; Blog</h3>
    <a>Great Land Auction Companies Make All the Difference</a>
    <a>Great OK Farms for Sale at Auction Prices</a>
    <a style="margin-top:12px">Farmland Auctions on Route 66</a>
    <a style="margin-top:13px">Great Land Auction Companies Make All the Difference</a>
  </div>
  <div class="rule"></div>
  <div class="side-block" style="padding-top:9px">
    <h3 class="side-h">Social Media</h3>
  </div>
  <div class="social">
    <span>Follow</span>
    <span>Feed</span>
    <span>Pins</span>
    <span>Posts</span>
    <span>Videos</span>
  </div>
</aside>

<footer class="footer abs">
  <nav><a>Home</a><i>|</i><a>Upcoming Auctions</a><i>|</i><a>Online Auctions</a><i>|</i><a>Real Estate</a><i>|</i><a>Services</a><i>|</i><a>About Us</a><i>|</i><a>Auction Gallery</a><i>|</i><a>Contact</a></nav>
  <div class="copy">Copyright © 2013 - 2013 Wellacombe auctioneers. All Rights Reserved</div>
  <div class="brand abs">
    <div class="brand-mark abs"></div>
    <div class="brand-name abs">WELLACOMBE<br>AUCTIONEERS</div>
    <div class="brand-tag abs">"The Bid That Counts!"</div>
    <div class="brand-partner abs">an alliance partner of Meridian Global</div>
  </div>
</footer>

</body>
</html>
```